Wix Design for a Clothing Design Web Marketing Site

We need a Wix design and content (including any images and copy) for a clothing design web storefront, Sew To Suit (or sewtosuit). Rough ideas and content can be found at http://marenvoltis.wix.com/sewtosuit.

Sew To Suit is an innovative business concept that combines fashion and entertainment. The business model allows customers to actively participate in the creation of fashion designs/concepts , visualize the garment in the customer’s body in 3D, and buy the physical garment made specially to fit the customer.
The fashion consultant will be able to create the design based on client's desires and test various possibilities (size, fabric, cut, etc..) in front of the customer, using software Drapova (the software is a key component of this business model)
(when developing the website use images from Drapova)
After the design is created, the customer can choose to order the actual piece. The garment will be made according to the created design, the customer measurements.

Target Market(s)

Primarily women from 25 to 45, who are fashion enthusiasts and appreciate fit and exclusivity. They are hedonistic shoppers, who shop for entertainment.
Men (metrosexuals) who are fashion enthusiasts, also hedonistic shoppers.

Industry/Entity Type

Clothing

Font styles to use
Serif
Sans Serif

Requirements
Must have
• Must have a landing page (home) or section, that gives the consumer an idea of what Sew To Suit will do for them, an about page or section that tells about the company and product, a how it works page or section that describes how it works (http://marenvoltis.wix.com/sewtosuit#!services3/c192y), and page or section about pricing, and a page or section on how to contact us.
Nice to have
• Very modern and clean. The website must be based on the main picture of the studio in the example. If that studio is the store, what will the website look like?
• Colors yellow, grey and white. Use the zig zag in yellow and white. You can change the size of the lines. The zig zagi gives the modern and bold accent. Outfits in pictures must show nicely tailored garments.

```html
<!DOCTYPE html>
<html lang="en">
<head>
<meta charset="utf-8">
<title>Sew To Suit</title>
<link rel="stylesheet" href="https://fonts.googleapis.com/css2?family=Federo&family=Poiret+One&family=Roboto+Condensed:wght@400;700&family=Roboto+Slab:wght@300;400&family=Open+Sans:wght@400;600&family=Lexend+Zetta&display=swap">
<style>
  :root{
    --yellow:#f6ec36;
    --yellow-soft:#ece66a;
    --slate:#55585c;
    --nav:#47494f;
    --sky:#53b0cc;
    --sky-dark:#4aa5c2;
    --header-bg:#ffffff;
    --header-panel:#f1f1f1;
    --ink:#2b2b2b;
    --white:#ffffff;
    --footer-bg:#f3f3f3;
    --footer-ink:#3a3a3a;
    --link:#1f3f7a;
    --bottom:#0c0c0c;
  }
  *{box-sizing:border-box;margin:0;padding:0}
  html,body{width:959px;height:1200px;overflow:hidden;background:var(--white)}
  body{position:relative;font-family:"Open Sans",sans-serif}

  .site-header{position:absolute;left:0;top:0;width:959px;height:135px;background:var(--header-bg);overflow:hidden}
  .site-header .panel{position:absolute;inset:0}
  .brand{position:absolute;left:96px;top:14px;width:210px;height:118px;text-align:center}
  .brand .mark{display:block;margin:0 auto;width:78px;height:78px;border-radius:50%;background:#b9b9b9;border:5px solid var(--white);box-shadow:0 0 0 1px #ddd}
  .brand .name{display:block;margin-top:8px;font-family:"Roboto Slab",serif;font-weight:400;font-size:22px;letter-spacing:1px;color:var(--ink)}
  .tagline{position:absolute;left:444px;top:30px;font-family:"Federo",sans-serif;font-size:37px;line-height:36px;color:#222}

  .main-nav{position:absolute;left:0;top:135px;width:959px;height:31px;background:var(--nav)}
  .main-nav a{position:absolute;top:0;height:31px;line-height:31px;font-family:"Roboto Condensed",sans-serif;font-size:13.5px;color:var(--white);text-decoration:none}
  .main-nav a.active{background:var(--sky);width:67px;text-align:center}

  .hero{position:absolute;left:0;top:166px;width:959px;height:323px;background:var(--sky)}
  .hero-frame{position:absolute;left:92px;top:28px;width:746px;height:262px;background:var(--white)}
  .hero-photo{position:absolute;left:7px;top:7px;width:732px;height:248px;background:linear-gradient(120deg,#f4f4f2 0%,#e6e3dc 45%,#d9c27a 70%,#efefec 100%)}
  .hero-copy{position:absolute;left:26px;top:88px;font-family:"Poiret One",sans-serif;color:var(--ink)}
  .hero-copy .line{display:block;font-size:20px;line-height:24px;letter-spacing:1px;font-weight:400}
  .hero-copy .big{font-size:30px;line-height:34px;font-weight:400}
  .hero-btn{position:absolute;left:27px;top:178px;width:112px;height:31px;background:#2a2a2a;color:var(--yellow);font-family:"Open Sans",sans-serif;font-size:12px;line-height:31px;text-align:center}
  .hero-arrow{position:absolute;top:133px}

  .step{position:absolute;width:180px;height:221px;background:var(--slate);text-align:center;color:var(--white)}
  .step .badge{position:absolute;left:50%;top:-28px;width:82px;height:82px;margin-left:-41px;border-radius:50%;background:var(--yellow);border:5px solid var(--white)}
  .step .badge svg{position:absolute;left:50%;top:50%;transform:translate(-50%,-50%)}
  .step h3{position:absolute;left:0;right:0;top:62px;font-family:"Roboto Slab",serif;font-weight:300;font-size:16px;color:var(--yellow-soft)}
  .step h3.lg{font-size:20px;top:58px}
  .step p{position:absolute;left:20px;right:20px;top:98px;font-size:12.5px;line-height:15.5px}
  .feature{position:absolute;width:171px;height:221px;background:radial-gradient(circle,#ffffff 60%,#fde9cf 100%);text-align:center}
  .feature .photo{position:absolute;left:30px;top:10px;width:111px;height:180px}
  .feature span{position:absolute;left:0;right:0;bottom:10px;font-family:"Roboto Slab",serif;font-weight:300;font-size:15px;color:#333}

  .site-footer{position:absolute;left:0;top:1029px;width:959px;height:136px;background:var(--footer-bg)}
  .site-footer h4{position:absolute;top:14px;font-family:"Roboto Condensed",sans-serif;font-weight:700;font-size:12px;color:#222}
  .site-footer ul{position:absolute;top:36px;list-style:none;font-size:9.5px;line-height:15.3px;color:var(--footer-ink)}
  .site-footer .link{color:var(--link)}
  .subscribe-input{position:absolute;left:467px;top:40px;width:181px;height:26px;border:1px solid #555;background:#ececec;font-size:8.5px;line-height:24px;padding-left:7px;color:#333}
  .subscribe-btn{position:absolute;left:467px;top:73px;width:73px;height:26px;background:var(--slate);color:var(--white);font-family:"Roboto Condensed",sans-serif;font-size:11px;line-height:26px;text-align:center}
  .footer-brand{position:absolute;left:673px;top:16px;width:152px;text-align:center}
  .footer-brand .mark{display:block;margin:0 auto;width:70px;height:70px;border-radius:50%;background:#b9b9b9;border:4px solid var(--white);box-shadow:0 0 0 1px #ddd}
  .footer-brand .name{display:block;margin-top:6px;font-family:"Roboto Slab",serif;font-size:17px;color:var(--ink);letter-spacing:1px}
  .legal{position:absolute;left:0;top:1165px;width:959px;height:35px;background:var(--bottom);color:#8a8a8a;font-size:8.5px;line-height:35px;text-align:center}
</style>
</head>
<body>

<header class="site-header">
  <svg class="panel" width="959" height="135" aria-hidden="true">
    <polygon points="437,0 959,0 959,135 380,135" fill="var(--header-panel)"/>
  </svg>
  <div class="brand">
    <span class="mark"></span>
    <span class="name">SEW TO SUIT</span>
  </div>
  <p class="tagline">Clothes made specially for<br>You and designed by you</p>
</header>

<nav class="main-nav">
  <a class="active" style="left:92px">Home</a>
  <a style="left:183px">What is Sew To Suit?</a>
  <a style="left:341px">How It Works?</a>
  <a style="left:453px">Price</a>
  <a style="left:520px">Contact Us</a>
</nav>

<section class="hero">
  <svg class="hero-arrow" style="left:35px" width="34" height="34" aria-hidden="true">
    <circle cx="17" cy="17" r="16" fill="none" stroke="#fff" stroke-width="1.5"/>
    <polyline points="20,9 12,17 20,25" fill="none" stroke="#fff" stroke-width="1.5"/>
  </svg>
  <svg class="hero-arrow" style="left:862px" width="34" height="34" aria-hidden="true">
    <circle cx="17" cy="17" r="16" fill="none" stroke="#fff" stroke-width="1.5"/>
    <polyline points="14,9 22,17 14,25" fill="none" stroke="#fff" stroke-width="1.5"/>
  </svg>
  <div class="hero-frame">
    <div class="hero-photo" role="img" aria-label="Bright white design studio with yellow-lit ceiling and consultation booths"></div>
    <div class="hero-copy" style="left:26px;top:85px">
      <span class="line">DESIGN YOUR OWN DRESS</span>
      <span class="line">&amp; SHOW YOUR CREATIVITY</span>
      <span class="line big">TO THE WORLD</span>
    </div>
    <div class="hero-btn">KNOW MORE</div>
  </div>
</section>

<main>
  <article class="step" style="left:103px;top:533px">
    <div class="badge"><svg width="34" height="36" viewBox="0 0 34 36" aria-hidden="true">
      <circle cx="17" cy="16" r="9" fill="none" stroke="#333" stroke-width="2.5"/>
      <rect x="13" y="25" width="8" height="5" fill="#333"/>
      <rect x="16" y="11" width="2" height="6" fill="#333"/><rect x="16" y="19" width="2" height="2" fill="#333"/>
      <g stroke="#333" stroke-width="2"><line x1="17" y1="1" x2="17" y2="4"/><line x1="4" y1="16" x2="1" y2="16"/><line x1="30" y1="16" x2="33" y2="16"/><line x1="7" y1="6" x2="5" y2="4"/><line x1="27" y1="6" x2="29" y2="4"/></g>
    </svg></div>
    <h3>Be Inspired</h3>
    <p>Be inspired by the latest trends, iconic styles from all eras and the most prestigious fashion shows</p>
  </article>
  <article class="step" style="left:287px;top:533px">
    <div class="badge"><svg width="40" height="36" viewBox="0 0 40 36" aria-hidden="true">
      <path d="M18 3C8 3 2 10 2 18c0 9 7 15 15 15 4 0 4-3 2-5s0-5 4-5h5c5 0 8-3 8-7C36 8 28 3 18 3z" fill="#333"/>
      <circle cx="10" cy="17" r="3" fill="var(--yellow)"/><circle cx="14" cy="10" r="3" fill="var(--yellow)"/><circle cx="23" cy="9" r="3" fill="var(--yellow)"/>
    </svg></div>
    <h3>Design</h3>
    <p>Learn about our unique process, where you become the designer</p>
  </article>
  <article class="step" style="left:471px;top:533px">
    <div class="badge"><svg width="40" height="28" viewBox="0 0 40 28" aria-hidden="true">
      <path d="M2 8h36c0 10-8 17-18 17S2 18 2 8z" fill="#333"/>
      <g fill="var(--yellow)"><circle cx="10" cy="13" r="1.4"/><circle cx="16" cy="16" r="1.4"/><circle cx="22" cy="13" r="1.4"/><circle cx="28" cy="16" r="1.4"/><circle cx="19" cy="20" r="1.4"/></g>
    </svg></div>
    <h3>Choose The Fabric</h3>
    <p>First rate fabrics &amp;<br>highest quality materials</p>
  </article>
  <figure class="feature" style="left:656px;top:533px">
    <div class="photo" role="img" aria-label="Tailored black sleeveless sheath dress" style="background:linear-gradient(180deg,#3a3a3a,#111 60%,#222)"></div>
    <span>Women Special</span>
  </figure>

  <article class="step" style="left:103px;top:794px">
    <div class="badge"><svg width="28" height="38" viewBox="0 0 28 38" aria-hidden="true">
      <path d="M9 2h10v6l3 6-3 3 7 18H2l7-18-3-3 3-6z" fill="#333"/>
    </svg></div>
    <h3>See Your Creation</h3>
    <p style="top:98px">See your creation in 3D</p>
  </article>
  <article class="step" style="left:287px;top:794px">
    <div class="badge"><svg width="40" height="34" viewBox="0 0 40 34" aria-hidden="true">
      <path d="M13 2l-11 6 4 9 5-2v18h18V15l5 2 4-9-11-6c-1 4-4 6-7 6s-6-2-7-6z" fill="#333"/>
    </svg></div>
    <h3 class="lg">Wear It</h3>
    <p style="top:98px">Wear your design, fitted for your exact body measurements</p>
  </article>
  <article class="step" style="left:471px;top:794px">
    <div class="badge"><svg width="34" height="36" viewBox="0 0 34 36" aria-hidden="true">
      <circle cx="11" cy="6" r="3.5" fill="#333"/><circle cx="23" cy="8" r="3.5" fill="#333"/>
      <path d="M8 11h6l1 10h-3l-1 12H9l-1-12z" fill="#333"/>
      <path d="M20 13h6l6 18H18z" fill="#333"/>
    </svg></div>
    <h3>Have Fun, Be Creative</h3>
    <p style="top:98px">First rate fabrics &amp;<br>highest quality materials</p>
  </article>
  <figure class="feature" style="left:656px;top:794px">
    <div class="photo" role="img" aria-label="Navy tailored suit jacket with shirt and tie on a dress form" style="background:linear-gradient(180deg,#e8e8e8 0%,#1e2b52 25%,#17213f 100%)"></div>
    <span>Men Special</span>
  </figure>
</main>

<footer class="site-footer">
  <h4 style="left:98px">QUICK LINKS</h4>
  <ul style="left:100px">
    <li>Home</li><li>What is Sew To Suit?</li><li>How It Works?</li><li>Price</li><li>Contact Us</li>
  </ul>
  <h4 style="left:266px">COMPANY INFO</h4>
  <ul style="left:268px">
    <li>58 Loom Ave,</li><li>2nd Floor, Suite 310</li><li>Portland, OR</li><li>USA</li>
    <li>Ph: <span class="link">503 2719 640</span></li>
    <li>Email: <span class="link">hello@sewtosuitstudio.com</span></li>
  </ul>
  <h4 style="left:466px">SUBSCRIBE NEWSLETTER</h4>
  <div class="subscribe-input">Type your email id</div>
  <div class="subscribe-btn">SUBMIT</div>
  <div class="footer-brand">
    <span class="mark"></span>
    <span class="name">SEW TO SUIT</span>
  </div>
</footer>
<div class="legal">© 2015, All Rights Reserved, Sew To Suit</div>

</body>
</html>
```